Need a clean & modern homepage for an education site + opportunity for longer term work

Thanks for viewing our project. We are excited about this new website and we hope that we might build a relationship with designers as we work on this project. I provided quite a few details and requirements to help you more quickly create a design that meets our needs.
Who we are:
We are a website that discusses the importance of college accreditation and provides a directory of college programs.
What we need:
A homepage that meets the below requirements and is inspired by the examples provided
Definition of accredited:
ac·cred·it·ed [uh-kred-i-tid] adj.
1. officially recognized as meeting the essential requirements, as of academic excellence: accredited schools.
2. provided with official credentials, as by a government: an accredited diplomatic representative.
3. accepted as authoritative: an accredited theory.
Overall look and feel for the homepage:
- Clean, simple and modern
- Limited (or zero) pictures
- Utilize color blocks with text
- A trend seems to be longer vertical length homepages with lots of whitespace. I generally like this trend as long as the page is not way to tall.
Inspirations: Sites that have a similar look and feel to what I need.
http://lernvoxa.org/
http://www.campusmetrik.com/colleges/brantmoor-university/
http://quietfolding.org/
http://www.velostrahiring.com/
http://www.zunq.com/
http://sketches.bxv.com/
Items to be included on the homepage. Details below on each item.
- Top navigation
- Logo: Please leave a blank area for a logo. The logo has not been designed.
- Simple graphic/color block at the top that highlights a definition of “Accredited” – the definition should be formatted like it is being copy/pasted from a dictionary.
- Space for a video and small (50 word) written description of the video. You can use placeholder text.
- One section with 3 Paragraphs of content (each paragraph around 100 words) with a header at the top. You can use placeholder text but please create the formatting. At the end of the 3 paragraphs please have a “Read More” Note this shouldn't be 3 separate paragraphs with three read mores - it is 3 paragraphs with one read more at the end.
- An area with the header “Search Colleges by State” that has anchor text links to all 50 states.
Top navigation:
- Home
- States – with a subnav dropdown that includes all 50 US states.
- Programs – with a subnav dropdown that includes program titles (list below)
- Degrees - with a subnav dropdown that includes 5 degree levels (list below)
- Accreditation – no subnav
- Rankings – no subnav
- Resources – no subnav
Footer
- Link to about us, privacy, and a copyright www.url.com
Programs List for sub navigation
Accounting
Art
Bible
Business
Criminal Justice
Design
Education
Engineering
English
Law
LPN to RN
Management
Math
MBA
MPH
Medical Assisting
Military
Nursing
Occupational Therapy
Paralegal
Psychology
Pharmacy
RN to BSN
Radiology
Social Work
Sonography
Degrees list for sub navigation
Certificate
Associate
Bachelors
Masters
PhD
Thanks so much - looking forward to working with you!
Education

```html
<!DOCTYPE html>
<html lang="en">
<head>
<meta charset="utf-8">
<title>My Website Name – Accredited Colleges</title>
<link href="https://fonts.googleapis.com/css2?family=Open+Sans:ital,wght@0,300;0,400;0,600;0,700;1,400&display=swap" rel="stylesheet">
<style>
:root{
  --blue:#1e9ad6;
  --blue-light:#35b3e6;
  --blue-deep:#1479b8;
  --navy:#0d4e86;
  --navy-dark:#0a3f6e;
  --green:#34b44a;
  --grey-bg:#eceff2;
  --text:#4a4a4a;
  --white:#ffffff;
}
*{box-sizing:border-box;margin:0;padding:0}
html,body{width:1200px;height:2400px;overflow:hidden}
body{font-family:"Open Sans",Arial,sans-serif;color:var(--text);background:var(--white)}
.page{position:relative;width:1200px;height:2400px}

/* header */
.site-header{height:90px;display:flex;align-items:flex-end;justify-content:space-between;padding:0 40px 22px;position:relative;background:var(--white)}
.site-name{font-size:24px;font-weight:700;color:var(--navy);letter-spacing:.5px}
.social{position:absolute;top:14px;right:42px;display:flex;gap:8px}
.social span{width:22px;height:22px;border-radius:50%;background:var(--green)}
.social span:nth-child(2){background:var(--blue)}
.social span:nth-child(3){background:var(--navy)}
.main-nav{display:flex;gap:26px;font-size:16px}
.main-nav a{color:var(--blue);text-decoration:none}

/* hero */
.hero{position:relative;height:470px;overflow:hidden}
.hero-scene{position:absolute;inset:0;background:linear-gradient(180deg,#6fb3e3 0%,#7fbfd8 60%,#7cb85a 100%)}
.definition-block{position:absolute;left:180px;top:38px;width:520px;padding:20px 26px;background:rgba(30,154,214,.9);color:var(--white)}
.definition-block .headword{font-size:24px;font-weight:700;line-height:1.2}
.definition-block .pron{font-size:15px;font-weight:400;margin-left:6px}
.definition-block .pos{font-size:15px;font-style:italic;font-weight:400;margin-left:4px}
.definition-block ol{margin-top:8px;padding-left:22px;font-size:14px;line-height:1.4}
.definition-block li{margin-bottom:3px}
.definition-block em{font-style:italic;opacity:.9}
.search-bar{position:absolute;left:200px;top:270px;display:flex;gap:14px;align-items:center}
.search-bar .field{height:40px;background:var(--white);border:1px solid #cfd6dc;font-size:14px;color:#777;padding:0 14px;display:flex;align-items:center;justify-content:space-between}
.search-bar .college{width:230px}
.search-bar .state{width:230px}
.search-bar .button{height:40px;padding:0 24px;background:var(--blue);color:var(--white);font-size:15px;font-weight:600;display:flex;align-items:center}

/* video */
.video-intro{height:160px;display:flex;align-items:center;padding:0 180px;gap:40px}
.video-intro p{width:470px;color:var(--blue);font-size:17px;line-height:1.25}
.video-box{position:relative;width:400px;height:120px}
.video-thumb{position:absolute;inset:0 0 38px 0;background:linear-gradient(90deg,var(--green) 0%,#7fd08e 60%,#d6efe0 100%)}
.play{position:absolute;left:260px;top:20px;width:40px;height:40px;border-radius:50%;background:var(--blue)}
.play svg{position:absolute;left:14px;top:11px}
.watch{position:absolute;left:150px;bottom:0;width:170px;height:32px;background:var(--blue-light);color:var(--white);font-size:17px;text-align:center;line-height:32px}

/* cards */
.features{height:270px;background:var(--grey-bg);display:flex;justify-content:center;gap:26px;padding-top:30px}
.card{width:270px;height:210px;background:var(--white);position:relative;padding:16px 18px}
.card-head{display:flex;gap:12px;align-items:center;margin-bottom:10px}
.card-icon{width:40px;height:40px;border:2px solid #777;border-radius:4px}
.card h3{font-size:18px;font-weight:600;color:#333;line-height:1}
.card h3 small{display:block;font-size:14px;font-weight:400;color:#666;margin-top:3px}
.card p{font-size:11px;line-height:1.35;color:#555}
.card .read-more{position:absolute;left:18px;right:18px;bottom:-12px;height:30px;background:var(--green);color:var(--white);font-size:16px;text-align:center;line-height:30px}

/* content section */
.content-section{position:relative;height:750px;background:linear-gradient(180deg,var(--blue) 0%,var(--blue-deep) 100%);color:var(--white);padding:56px 200px 0 130px}
.plus{position:absolute;left:583px;top:-17px;width:34px;height:34px;border-radius:50%;background:var(--white);border:2px solid #ccc}
.plus svg{position:absolute;left:8px;top:8px}
.content-section h2{font-size:34px;font-weight:600;margin-bottom:22px}
.topic{display:flex;gap:34px;margin-bottom:22px}
.topic-icon{width:70px;flex:none;padding-top:24px}
.topic h3{font-size:22px;font-weight:600;margin-bottom:8px}
.topic p{font-size:13px;line-height:1.45;width:760px}
.content-read-more{display:flex;justify-content:flex-end;margin-right:-50px}
.content-read-more span{font-size:44px;font-weight:300;background:rgba(255,255,255,.12);padding:0 12px;line-height:1.1}
.down-arrow{position:absolute;left:580px;bottom:-20px}

/* directory */
.directory{height:300px;background:var(--navy);color:var(--white);display:flex;padding:60px 120px 0;gap:90px}
.directory h4{font-size:22px;font-weight:600;margin-bottom:10px;padding-left:20px}
.directory .cols{display:flex;gap:80px;border-top:1px solid rgba(255,255,255,.35);padding:12px 20px 0}
.directory ul{list-style:none;font-size:15px;line-height:1.3}
.directory section{width:440px}

/* states */
.states{height:260px;background:var(--navy-dark);display:flex;padding:26px 120px 0;gap:40px}
.states h4{font-size:22px;font-weight:600;color:var(--white);display:flex;gap:10px;align-items:center;margin-bottom:12px}
.state-grid{display:grid;grid-template-columns:repeat(4,140px);gap:8px 14px}
.state-grid a{height:22px;background:#6d93b8;color:var(--white);font-size:12px;text-align:center;line-height:22px;text-decoration:none}
.us-map{width:300px;height:170px;margin-top:40px;background:linear-gradient(135deg,#6f95ba,#4f7aa3);border-radius:30px 60px 40px 20px}

/* footer */
.site-footer{height:100px;background:var(--green);color:var(--white);display:flex;justify-content:space-between;align-items:center;padding:0 120px;font-size:24px}
.site-footer nav{display:flex;gap:30px}
</style>
</head>
<body>
<div class="page">

<header class="site-header">
  <div class="site-name">MY WEBSITE NAME</div>
  <div class="social"><span></span><span></span><span></span></div>
  <nav class="main-nav">
    <a href="#">Home</a><a href="#">States</a><a href="#">Programs</a><a href="#">Degrees</a><a href="#">Accreditation</a><a href="#">Rankings</a><a href="#">Resources</a>
  </nav>
</header>

<section class="hero">
  <div class="hero-scene" role="img" aria-label="Background photo of open sky above green fields"></div>
  <div class="definition-block">
    <div class="headword">ac·cred·it·ed<span class="pron">[uh-kred-i-tid]</span><span class="pos">adj.</span></div>
    <ol>
      <li>officially recognized as meeting the essential requirements, as of academic excellence: <em>accredited schools.</em></li>
      <li>provided with official credentials, as by a government: <em>an accredited diplomatic representative.</em></li>
      <li>accepted as authoritative: <em>an accredited theory.</em></li>
    </ol>
  </div>
  <div class="search-bar">
    <div class="field college">Search College</div>
    <div class="field state">State <span>▾</span></div>
    <div class="button">SEARCH</div>
  </div>
</section>

<section class="video-intro">
  <p>written description of the video written description of the video written description of the video written description of the video written description of the video written description of the video</p>
  <div class="video-box">
    <div class="video-thumb" role="img" aria-label="Video still of a presenter"></div>
    <div class="play"><svg width="14" height="18" viewBox="0 0 14 18"><path d="M0 0L14 9L0 18Z" fill="#fff"/></svg></div>
    <div class="watch">Watch video</div>
  </div>
</section>

<section class="features">
  <article class="card">
    <div class="card-head"><div class="card-icon"></div><h3>Rankings<small>explain small desc</small></h3></div>
    <p>One section with 3 Paragraphs of content (each paragraph around 100 words) with a header at the top. You can use placeholder text but please create the formatting. At the end of the 3 paragraphs please have a “Read More”. Note this shouldn’t be 3 separate paragraphs with three read mores.</p>
    <div class="read-more">Read More</div>
  </article>
  <article class="card">
    <div class="card-head"><div class="card-icon"></div><h3>Accreditation<small>explain small desc</small></h3></div>
    <p>One section with 3 Paragraphs of content (each paragraph around 100 words) with a header at the top. You can use placeholder text but please create the formatting. At the end of the 3 paragraphs please have a “Read More”. Note this shouldn’t be 3 separate paragraphs with three read mores.</p>
    <div class="read-more">Read More</div>
  </article>
  <article class="card">
    <div class="card-head"><div class="card-icon"></div><h3>Resources<small>explain small desc</small></h3></div>
    <p>One section with 3 Paragraphs of content (each paragraph around 100 words) with a header at the top. You can use placeholder text but please create the formatting. At the end of the 3 paragraphs please have a “Read More”. Note this shouldn’t be 3 separate paragraphs with three read mores.</p>
    <div class="read-more">Read More</div>
  </article>
</section>

<section class="content-section">
  <div class="plus"><svg width="14" height="14" viewBox="0 0 14 14"><path d="M7 0V14M0 7H14" stroke="#888" stroke-width="3"/></svg></div>
  <h2>header at the top</h2>
  <div class="topic">
    <div class="topic-icon"><svg width="70" height="54" viewBox="0 0 70 54"><rect x="10" y="4" width="50" height="34" rx="2" fill="none" stroke="#fff" stroke-width="4"/><path d="M2 44H68L62 50H8Z" fill="#fff"/></svg></div>
    <div><h3>header at the top</h3>
    <p>One section with 3 Paragraphs of content (each paragraph around 100 words) with a header at the top. You can use placeholder text but please create the formatting. At the end of the 3 paragraphs please have a “Read More”. Note this shouldn’t be 3 separate paragraphs with three read mores – it is 3 paragraphs with one read more at the end. One section with 3 Paragraphs of content with a header at the top. You can use placeholder text but please create the formatting. At the end of the 3 paragraphs please have a “Read More”. Note this shouldn’t be 3 separate paragraphs with three read mores – it is 3 paragraphs with one read more at the end.</p></div>
  </div>
  <div class="topic">
    <div class="topic-icon"><svg width="70" height="54" viewBox="0 0 70 54"><circle cx="20" cy="12" r="8" fill="#fff"/><rect x="8" y="24" width="24" height="26" rx="4" fill="#fff"/><rect x="38" y="6" width="30" height="20" fill="none" stroke="#fff" stroke-width="3"/><path d="M34 30L46 22" stroke="#fff" stroke-width="3"/></svg></div>
    <div><h3>header at the top</h3>
    <p>One section with 3 Paragraphs of content (each paragraph around 100 words) with a header at the top. You can use placeholder text but please create the formatting. At the end of the 3 paragraphs please have a “Read More”. Note this shouldn’t be 3 separate paragraphs with three read mores – it is 3 paragraphs with one read more at the end. One section with 3 Paragraphs of content with a header at the top. You can use placeholder text but please create the formatting. At the end of the 3 paragraphs please have a “Read More”. Note this shouldn’t be 3 separate paragraphs with three read mores – it is 3 paragraphs with one read more at the end.</p></div>
  </div>
  <div class="topic">
    <div class="topic-icon"><svg width="70" height="54" viewBox="0 0 70 54"><path d="M35 4L68 18L35 32L2 18Z" fill="#fff"/><path d="M16 26V40Q35 50 54 40V26L35 34Z" fill="#fff"/><path d="M62 21V40" stroke="#fff" stroke-width="3"/></svg></div>
    <div><h3>header at the top</h3>
    <p>One section with 3 Paragraphs of content (each paragraph around 100 words) with a header at the top. You can use placeholder text but please create the formatting. At the end of the 3 paragraphs please have a “Read More”. Note this shouldn’t be 3 separate paragraphs with three read mores – it is 3 paragraphs with one read more at the end. One section with 3 Paragraphs of content with a header at the top. You can use placeholder text but please create the formatting. At the end of the 3 paragraphs please have a “Read More”. Note this shouldn’t be 3 separate paragraphs with three read mores – it is 3 paragraphs with one read more at the end.</p></div>
  </div>
  <div class="content-read-more"><span>Read More</span></div>
  <svg class="down-arrow" width="40" height="22" viewBox="0 0 40 22"><path d="M0 0H40L20 22Z" fill="#1479b8"/></svg>
</section>

<section class="directory">
  <section>
    <h4>Programs</h4>
    <div class="cols">
      <ul><li>Accounting</li><li>Art</li><li>Bible</li><li>Business</li><li>Criminal justice</li><li>Design</li><li>Education</li><li>Engineering</li></ul>
      <ul><li>Accounting</li><li>Art</li><li>Bible</li><li>Business</li><li>Criminal justice</li><li>Design</li><li>Education</li><li>Engineering</li></ul>
    </div>
  </section>
  <section>
    <h4>Degrees</h4>
    <div class="cols">
      <ul><li>Accounting</li><li>Art</li><li>Bible</li><li>Business</li><li>Criminal justice</li><li>Design</li><li>Education</li><li>Engineering</li></ul>
      <ul><li>Accounting</li><li>Art</li><li>Bible</li><li>Business</li><li>Criminal justice</li><li>Design</li><li>Education</li><li>Engineering</li></ul>
    </div>
  </section>
</section>

<section class="states">
  <div>
    <h4><svg width="18" height="18" viewBox="0 0 18 18"><circle cx="7" cy="7" r="5" fill="none" stroke="#fff" stroke-width="2.5"/><path d="M11 11L17 17" stroke="#fff" stroke-width="2.5"/></svg>Colleges by State</h4>
    <div class="state-grid">
      <a href="#">state</a><a href="#">state</a><a href="#">state</a><a href="#">state</a>
      <a href="#">state</a><a href="#">state</a><a href="#">state</a><a href="#">state</a>
      <a href="#">state</a><a href="#">state</a><a href="#">state</a><a href="#">state</a>
      <a href="#">state</a><a href="#">state</a><a href="#">state</a><a href="#">state</a>
      <a href="#">state</a><a href="#">state</a><a href="#">state</a><a href="#">state</a>
      <a href="#">state</a><a href="#">state</a><a href="#">state</a><a href="#">state</a>
    </div>
  </div>
  <div class="us-map" role="img" aria-label="Map of the United States"></div>
</section>

<footer class="site-footer">
  <div>copyright@www.url.com</div>
  <nav><span>about us</span><span>privacy</span></nav>
</footer>

</div>
</body>
</html>
```